Heron Loan Partners Business Card

We need a business card design for our mortgage servicing company. In addition to servicing the loans of homeowners, we help homeowners with purchasing their homes and any mortgage refinancing. We would like to see designs that use the colors in the logo attached below (gold-ish yellow and navy blue), and any other design you deem fit! The design should communicate a simpler life with smart mortgages provided by Heron.

```html
<!DOCTYPE html>
<html lang="en">
<head>
<meta charset="utf-8">
<title>Heron Loan Partners – Business Card</title>
<link href="https://fonts.googleapis.com/css2?family=Open+Sans:wght@400;600;700&display=swap" rel="stylesheet">
<style>
  :root {
    --navy: #262057;
    --gold: #e0b13c;
    --paper: #ffffff;
    --ink: #1c1c1c;
    --backdrop: #333333;
  }
  * { box-sizing: border-box; margin: 0; padding: 0; }
  html, body { width: 1200px; height: 780px; overflow: hidden; }
  body {
    background: var(--backdrop);
    font-family: "Open Sans", Arial, sans-serif;
    position: relative;
  }
  .card {
    position: absolute;
    top: 230px;
    width: 540px;
    height: 309px;
    background: var(--paper);
    overflow: hidden;
    box-shadow: 0 6px 18px rgba(0,0,0,.45);
  }
  .card--back { left: 40px; }
  .card--front { left: 620px; }

  /* back */
  .brand-large {
    position: absolute; inset: 0;
    display: flex; align-items: center; justify-content: center; gap: 16px;
  }
  .brand-large__dot { width: 26px; height: 26px; border-radius: 50%; background: var(--navy); }
  .brand-large__name { font-weight: 700; font-size: 64px; color: var(--gold); letter-spacing: 1px; }

  /* front */
  .brand-small {
    position: absolute; left: 34px; top: 52px;
    display: flex; align-items: center; gap: 9px;
  }
  .brand-small__dot { width: 13px; height: 13px; border-radius: 50%; background: var(--navy); }
  .brand-small__name { font-weight: 700; font-size: 34px; color: var(--gold); }

  .holder { position: absolute; right: 40px; top: 92px; text-align: right; }
  .holder__name { font-weight: 700; font-size: 25px; line-height: 1.1; }
  .holder__first { color: var(--gold); }
  .holder__last { color: var(--navy); }
  .holder__title { font-weight: 600; font-size: 15px; color: var(--ink); margin-top: 2px; }
  .holder-bar {
    position: absolute; right: 14px; top: 90px;
    width: 14px; height: 50px; background: var(--gold);
  }
  .rule {
    position: absolute; left: 40px; right: 38px; top: 148px;
    height: 1.5px; background: var(--navy);
  }
  .address {
    position: absolute; right: 40px; top: 170px; text-align: right;
    font-size: 14px; line-height: 1.35; color: var(--ink);
  }
  .contacts { position: absolute; left: 40px; top: 168px; list-style: none; }
  .contacts li {
    display: flex; align-items: center; gap: 10px;
    font-size: 14px; line-height: 1.45; color: var(--ink);
  }
  .contacts svg { width: 14px; height: 14px; flex: none; }
  .base-band { position: absolute; left: 0; bottom: 0; width: 540px; height: 70px; }
</style>
</head>
<body>

<section class="card card--back" aria-label="Card back">
  <div class="brand-large">
    <span class="brand-large__dot"></span>
    <span class="brand-large__name">Heron</span>
  </div>
</section>

<section class="card card--front" aria-label="Card front">
  <div class="brand-small">
    <span class="brand-small__dot"></span>
    <span class="brand-small__name">Heron</span>
  </div>

  <div class="holder-bar"></div>
  <div class="holder">
    <p class="holder__name"><span class="holder__first">Lena</span> <span class="holder__last">Marsh</span></p>
    <p class="holder__title">Managing Director</p>
  </div>

  <div class="rule"></div>

  <ul class="contacts">
    <li>
      <svg viewBox="0 0 16 16" aria-hidden="true"><path fill="#e0b13c" d="M3.5 1.5l2.5 2.6-1.4 1.8c.8 1.8 2.2 3.2 4 4l1.8-1.4 2.6 2.5-1.6 2.2C6.6 13 3 9.4 1.3 3.1z"/></svg>
      (555) 410-2286
    </li>
    <li>
      <svg viewBox="0 0 16 16" aria-hidden="true"><rect x="1" y="3.5" width="14" height="9.5" rx="1" fill="#e0b13c"/><path d="M1.5 4l6.5 5 6.5-5" stroke="#fff" stroke-width="1.2" fill="none"/></svg>
      info@heronloan.com
    </li>
    <li>
      <svg viewBox="0 0 16 16" aria-hidden="true"><circle cx="8" cy="8" r="7" fill="#e0b13c"/><path d="M1 8h14M8 1c-3 3.5-3 10.5 0 14M8 1c3 3.5 3 10.5 0 14" stroke="#fff" stroke-width="1" fill="none"/></svg>
      www.heronloan.com
    </li>
  </ul>

  <address class="address" style="font-style:normal">
    840 Linden Ave. Suite 300<br>
    Brookfield, TX 75010
  </address>

  <svg class="base-band" viewBox="0 0 540 70" aria-hidden="true">
    <path d="M0 52 L380 52 Q388 52 390 46 L394 38 Q396 32 404 32 L540 32 L540 70 L0 70 Z" fill="#262057"/>
    <path d="M0 42 L378 42 Q385 42 387 38 L390 32 L384 32 Q380 38 374 38 L0 38 Z" fill="#e0b13c"/>
  </svg>
</section>

</body>
</html>
```